LDI Illustration Web Design

Create illustration web design company for Lumaviro Darsa Informatika (LDI). I more prefer design with illustration concept. Detail for requirement please see attach file. I'm also attach LDI logo. This logo had 2 type, 2D design and 3D design. You can chose one of them, or used both.
For the winner or had good design would be possible to private project to completeness this website
Attach file requirement is guidance for design, but any changes are welcome
Updates
Sorry, I forgot about contact. Please add menu contact. You can put this menu besides login menu or part of menu level #1, or put on some where to adjust your design. Menu contact will give pop up window to email LDI Company and Company Information (Address, Telephone, etc)
Target Market(s)
Company (Business To Business)
Industry/Entity Type
It Company
Look and feel
Each slider illustrates characteristics of the customer's brand and the style your logo design should communicate.

```html
<!DOCTYPE html>
<html lang="en">
<head>
<meta charset="utf-8">
<title>LDI – Clients</title>
<link href="https://fonts.googleapis.com/css2?family=Arimo:wght@400;700&display=swap" rel="stylesheet">
<style>
:root{
  --navy:#0a6596;
  --sky-top:#bfe9f4;
  --sky-low:#9fdcee;
  --leaf:#7aac32;
  --leaf-btn:#8dba45;
  --grass-light:#c8f07a;
  --grass:#5e9d16;
  --footer-bar:#4b850d;
  --ink:#5b5b5b;
  --white:#ffffff;
  --frame:#dedede;
}
*{margin:0;padding:0;box-sizing:border-box}
html,body{width:1200px;height:1050px;overflow:hidden}
body{font-family:"Arimo",Arial,sans-serif;position:relative;background:var(--sky-top)}
.sky{position:absolute;left:0;top:0;width:1200px;height:700px;
  background:
    radial-gradient(ellipse 200px 45px at 120px 20px,rgba(255,255,255,.85),rgba(255,255,255,0)),
    radial-gradient(ellipse 170px 45px at 1060px 70px,rgba(255,255,255,.85),rgba(255,255,255,0)),
    radial-gradient(ellipse 150px 35px at 520px 30px,rgba(255,255,255,.7),rgba(255,255,255,0)),
    linear-gradient(180deg,#e3f6fb 0%,var(--sky-top) 20%,var(--sky-low) 60%,#b6e6f2 100%)}
.top-stripe{position:absolute;left:0;top:0;width:1200px;height:7px;background:var(--navy)}
.account-tab{position:absolute;left:757px;top:0;width:277px;height:36px}
.account-tab svg{position:absolute;left:0;top:0}
.account-tab a{position:absolute;top:9px;color:var(--white);font-weight:700;font-size:14px;text-decoration:none;white-space:nowrap}
.brand{position:absolute;left:165px;top:32px;display:flex;align-items:center;gap:12px}
.brand-mark{width:56px;height:56px;border-radius:50%;background:var(--navy)}
.brand-name{font-weight:700;font-size:58px;color:var(--leaf);letter-spacing:2px;line-height:1}
.scenery{position:absolute;left:0;top:620px;width:1200px;height:160px;
  background:
    radial-gradient(ellipse 70px 50px at 1150px 50px,#6fb042,rgba(111,176,66,0)),
    radial-gradient(ellipse 60px 30px at 50px 60px,#7cc48a,rgba(124,196,138,0)),
    linear-gradient(180deg,rgba(120,190,90,0) 0%,#8ccf5a 40%,var(--grass-light) 62%,#9ed64e 82%,var(--grass) 100%)}
.panel{position:absolute;left:137px;top:175px;width:812px;height:543px;background:var(--white);
  border-radius:4px;box-shadow:0 0 8px rgba(0,0,0,.18)}
.panel h1{position:absolute;left:36px;top:40px;font-size:26px;font-weight:700;color:var(--leaf)}
.panel .intro{position:absolute;left:38px;top:89px;width:730px;font-size:12px;line-height:17px;color:var(--ink)}
.client{position:absolute;width:360px;height:170px}
.client .photo{position:absolute;left:0;top:0;width:186px;height:170px;border:1px solid var(--frame);padding:6px;background:#f7f7f7}
.client .photo div{width:100%;height:100%}
.client .info{position:absolute;top:7px}
.client h2{font-size:13px;font-weight:700;color:var(--navy);line-height:17px;white-space:nowrap}
.client .role{font-size:12px;color:var(--leaf);line-height:17px;white-space:nowrap}
.client p{margin-top:8px;font-size:12px;line-height:16.6px;color:var(--ink);width:130px}
.read-more{position:absolute;left:601px;top:473px;width:104px;height:30px;background:var(--navy);color:var(--white);
  font-weight:700;font-size:14px;text-align:center;line-height:30px;border-radius:2px}
.main-nav{position:absolute;left:958px;top:179px;width:104px}
.main-nav a{display:block;height:30px;margin-bottom:8px;background:var(--navy);color:var(--white);font-weight:700;font-size:14px;
  text-align:center;line-height:28px;text-decoration:none;border:1px solid #0d5e8a}
.main-nav a.current{background:var(--leaf-btn);border-color:#79a63a}
.site-footer{position:absolute;left:0;top:776px;width:1200px;height:229px;background:linear-gradient(180deg,#5c9e12,#5e9b18)}
.footer-col{position:absolute;top:63px}
.footer-col h3{font-size:12.5px;font-weight:700;color:var(--white);padding-bottom:5px;border-bottom:1px dotted rgba(255,255,255,.6);width:141px}
.footer-col ul{list-style:none;margin-top:18px}
.footer-col li{font-size:11.5px;line-height:16.6px;color:var(--white)}
.social li{display:flex;align-items:center;gap:10px;height:28px;border-bottom:1px solid rgba(255,255,255,.15);width:152px;line-height:1}
.social ul{margin-top:10px}
.social .ico{width:17px;height:17px;border-radius:2px}
.legal{position:absolute;left:0;top:1005px;width:1200px;height:45px;background:var(--footer-bar);color:var(--white);
  font-size:11.5px;text-align:center;line-height:38px;border-top:1px solid #4f8a12}
</style>
</head>
<body>
<div class="sky" role="img" aria-label="Illustrated sky with soft white clouds"></div>
<div class="top-stripe"></div>
<div class="account-tab">
  <svg width="277" height="36" viewBox="0 0 277 36" aria-hidden="true">
    <path d="M0 0 H277 L257 26 Q251 34 241 34 H36 Q26 34 20 26 Z" fill="var(--navy)"/>
    <line x1="104" y1="7" x2="104" y2="28" stroke="#8fc3de" stroke-dasharray="2 2"/>
    <line x1="170" y1="7" x2="170" y2="28" stroke="#8fc3de" stroke-dasharray="2 2"/>
  </svg>
  <a href="#" style="left:42px">Sign In</a>
  <a href="#" style="left:114px">Contact</a>
  <a href="#" style="left:180px">Register Now!</a>
</div>
<div class="brand"><div class="brand-mark"></div><div class="brand-name">LDI</div></div>
<div class="scenery" role="img" aria-label="Illustrated hills of trees and grass meadow"></div>

<main class="panel">
  <h1>Clients</h1>
  <p class="intro">Getty uis aute irure dolor in reprehenderit in voluptate velit esse cillum dolore euitife. Duis aute irure dolor in reprehenderit in voluptate velit esse cillum dolore.Getty uis aute irure dolor in reprehenderit in voluptate velit esse cillum dolore euitife.</p>

  <div class="client" style="left:37px;top:142px">
    <div class="photo"><div role="img" aria-label="Portrait of a smiling businessman" style="background:linear-gradient(160deg,#e9e4d8,#b89a80 55%,#283347)"></div></div>
    <div class="info" style="left:200px"><h2>LOREM IPSUM DOLOR</h2><div class="role">Sed do eiusmod tempo</div><p>Lorem ipsum dolor sit amet consum dolsum redol sectetur</p></div>
  </div>
  <div class="client" style="left:391px;top:142px">
    <div class="photo"><div role="img" aria-label="Portrait of a smiling businesswoman" style="background:linear-gradient(160deg,#f1f1f1,#c79c80 50%,#3a3f4b)"></div></div>
    <div class="info" style="left:207px"><h2>LOREM IPSUM DOLOR</h2><div class="role">Sed do eiusmod tempo</div><p>Lorem ipsum dolor sit amet consum dolsum redol sectetur</p></div>
  </div>
  <div class="client" style="left:37px;top:337px">
    <div class="photo"><div role="img" aria-label="Portrait of a smiling man in a suit" style="background:linear-gradient(170deg,#f6f6f6,#8a6a50 55%,#5b4c35)"></div></div>
    <div class="info" style="left:200px"><h2>LOREM IPSUM DOLOR</h2><div class="role">Sed do eiusmod tempo</div><p>Lorem ipsum dolor sit amet consum dolsum redol sectetur</p></div>
  </div>
  <div class="client" style="left:391px;top:337px">
    <div class="photo"><div role="img" aria-label="Portrait of a smiling man at an office desk" style="background:linear-gradient(160deg,#7d8a94,#b58a6c 45%,#dfe5ea)"></div></div>
    <div class="info" style="left:207px"><h2>LOREM IPSUM DOLOR</h2><div class="role">Sed do eiusmod tempo</div><p>Lorem ipsum dolor sit amet consum dolsum redol sectetur</p></div>
  </div>
  <div class="read-more">Read More</div>
</main>

<nav class="main-nav">
  <a href="#">Home</a><a href="#">Services</a><a href="#">Product</a><a href="#" class="current">CLIENTS</a><a href="#">Company</a><a href="#">Blog</a>
</nav>

<footer class="site-footer">
  <div class="footer-col" style="left:211px"><h3>USEFUL LINKS</h3>
    <ul><li>Home</li><li>Products</li><li>Accessories</li><li>Our Story</li><li>Questions</li><li>Blog</li><li>Where We Are</li></ul></div>
  <div class="footer-col" style="left:523px"><h3>CATEGORIES</h3>
    <ul><li>LInk-1</li><li>LInk-1</li><li>LInk-1</li><li>LInk-1</li><li>LInk-1</li><li>LInk-1</li><li>LInk-1</li></ul></div>
  <div class="footer-col social" style="left:829px;top:60px"><h3>SOCIAL NETWORK</h3>
    <ul>
      <li><span class="ico" style="background:#f06a24"></span>Bolg : @ldi</li>
      <li><span class="ico" style="background:#3b5b9a"></span>Join us on Circlely</li>
      <li><span class="ico" style="background:#1b73ae"></span>Join us on Linkwork</li>
      <li><span class="ico" style="background:#5cc6e8"></span>Chirper : @ldi</li>
    </ul></div>
</footer>
<div class="legal">© 2007–2013, ldinforma.com.au. All Rights Reserved</div>
</body>
</html>
```